Brightway Haus Inc. Business Card Design

Brightway Haus Inc. is in search of a great clean design for our business cards!

Looking to incorporate our full logo and watermark on side one (however, I am open to having the text and watermark separated within the design.)

On side two, I am looking to have contact information (Name, Position, Phone #, Email, Website (www.thebrightwayhaus.ca). Can have the logo and/or watermark as part of the design if applicable.

Please add tagline "Where Shine Counts" on either side 1 or 2. This tagline can be in a sans serif, serif or cursive font as long as it compliments overall design. Capitalization can be title or sentence case depending on how it fits within the design.

Get creative!! Looking for a clean, crisp, premium design! Looking for a glossy card finish with spot UV features when printed. Cards will also be printed with rounded corners. Standard dimensions (3.5 x 2).

Target Market(s)

B2B - primary clients are business owners or property management corporations. (residential jobs are few and far between)

Industry/Entity Type

Business

Contact Information for Business Card

- clean, crisp design
- double sided
- spot UV accents and glossy finish upon printing
- standard business card size (3.5 x 2) with rounded corners
- please see project description for requirements per side

Font styles to use
Sans Serif

Requirements
Must have
• - adequate bleeds with print ready files
• - cohesive design elements between side 1 & 2
• - spot UV elements (can be on both sides or just one, use your discretion)
• - colour pallet should match the logo file provided
• - incorporate tagline "where shine counts" (this tagline can be in a serif or sans serif font as long as it is complimentary to the overall design.
Nice to have
• - Premium elements with a clean design
Should not have
• - Please omit cartoon or whimsical like designs, think premium.
• - Colours should not stray from the pallet of the provided logo.

```html
<!DOCTYPE html>
<html lang="en">
<head>
<meta charset="utf-8">
<title>Brightway Haus Inc. – Business Card</title>
<link rel="stylesheet" href="https://fonts.googleapis.com/css2?family=Open+Sans:wght@700;800&family=Roboto:wght@400;500;700&display=swap">
<style>
  :root {
    --teal: #0f9ea3;
    --teal-deep: #0b8f94;
    --navy: #1c1f4a;
    --card-white: #f4f4f4;
    --ink: #1e1e1e;
    --backdrop: #e6e6e6;
  }
  * { box-sizing: border-box; margin: 0; padding: 0; }
  html, body { width: 1200px; height: 576px; overflow: hidden; }
  body {
    background: var(--backdrop);
    position: relative;
    font-family: "Roboto", Arial, sans-serif;
  }
  .card {
    position: absolute;
    top: 138px;
    width: 484px;
    height: 293px;
    border-radius: 12px;
    overflow: hidden;
  }
  /* Side one */
  .card-front {
    left: 82px;
    background: var(--teal);
    display: flex;
    align-items: center;
    justify-content: center;
  }
  .wordmark {
    display: flex;
    align-items: center;
    gap: 10px;
  }
  .wordmark-square {
    width: 30px;
    height: 30px;
    background: var(--navy);
  }
  .wordmark-name {
    font-family: "Open Sans", Arial, sans-serif;
    font-weight: 800;
    font-size: 33px;
    letter-spacing: -0.5px;
    color: #ffffff;
    white-space: nowrap;
  }
  /* Side two */
  .card-back {
    left: 602px;
    background: var(--card-white);
  }
  .brand-panel {
    position: absolute;
    left: 0; top: 0;
    width: 226px; height: 293px;
  }
  .back-header {
    position: absolute;
    right: 30px;
    top: 34px;
    text-align: right;
  }
  .back-name-mark {
    font-family: "Open Sans", Arial, sans-serif;
    font-weight: 800;
    font-size: 23px;
    letter-spacing: -0.4px;
    color: var(--teal);
    line-height: 1;
    white-space: nowrap;
  }
  .tagline {
    margin-top: 6px;
    font-family: "Open Sans", Arial, sans-serif;
    font-weight: 700;
    font-size: 10px;
    letter-spacing: 2.4px;
    color: var(--navy);
    white-space: nowrap;
  }
  .person {
    position: absolute;
    right: 30px;
    top: 114px;
    text-align: right;
  }
  .person-name {
    font-family: "Roboto", Arial, sans-serif;
    font-weight: 700;
    font-size: 20px;
    color: var(--teal);
  }
  .person-role {
    margin-top: 3px;
    font-size: 11.5px;
    color: var(--ink);
  }
  .contacts {
    position: absolute;
    right: 30px;
    top: 174px;
    list-style: none;
    text-align: right;
    font-size: 12.5px;
    color: var(--ink);
  }
  .contacts li {
    display: flex;
    justify-content: flex-end;
    align-items: center;
    gap: 6px;
    height: 18px;
    white-space: nowrap;
  }
  .contacts .icon { width: 11px; height: 11px; fill: var(--teal); flex: none; }
  .contacts .accent { color: var(--teal); }
  .address {
    position: absolute;
    right: 30px;
    top: 236px;
    font-style: normal;
    text-align: right;
    font-size: 12.5px;
    line-height: 17px;
    color: var(--ink);
  }
</style>
</head>
<body>

  <section class="card card-front" aria-label="Business card side one">
    <div class="wordmark">
      <span class="wordmark-square" aria-hidden="true"></span>
      <span class="wordmark-name">BRIGHTWAY HAUS INC.</span>
    </div>
  </section>

  <section class="card card-back" aria-label="Business card side two">
    <svg class="brand-panel" viewBox="0 0 226 293" role="img" aria-label="Brand watermark area in teal and navy">
      <defs>
        <linearGradient id="panelTone" x1="0" y1="0" x2="0.4" y2="1">
          <stop offset="0" stop-color="#0f9ea3"/>
          <stop offset="0.6" stop-color="#0b8f94"/>
          <stop offset="1" stop-color="#1c1f4a"/>
        </linearGradient>
      </defs>
      <polygon points="0,0 226,0 166,293 0,293" fill="url(#panelTone)"/>
    </svg>

    <header class="back-header">
      <div class="back-name-mark">BRIGHTWAY HAUS</div>
      <div class="tagline">Where Shine Counts</div>
    </header>

    <div class="person">
      <div class="person-name">Daniel Reyes</div>
      <div class="person-role">Managing Director</div>
    </div>

    <ul class="contacts">
      <li>1800-555-0142
        <svg class="icon" viewBox="0 0 12 12" aria-hidden="true"><path d="M2.5 1h2l1 3-1.3 1a6.5 6.5 0 0 0 2.8 2.8l1-1.3 3 1v2c0 .6-.4 1-1 1A9.5 9.5 0 0 1 1.5 2c0-.6.4-1 1-1z"/></svg>
      </li>
      <li>daniel@brightwayhaus.ca
        <svg class="icon" viewBox="0 0 12 12" aria-hidden="true"><path d="M1 2.5h10v7H1z M1.6 3 6 6.5 10.4 3" stroke="#f4f4f4" stroke-width="0.9"/></svg>
      </li>
      <li><span>www.<span class="accent">thebrightwayhaus</span>.ca</span>
        <svg class="icon" viewBox="0 0 12 12" aria-hidden="true"><circle cx="6" cy="6" r="5"/><path d="M1 6h10M6 1c-2.6 2.8-2.6 7.2 0 10M6 1c2.6 2.8 2.6 7.2 0 10" stroke="#f4f4f4" stroke-width="0.8" fill="none"/></svg>
      </li>
    </ul>

    <address class="address">
      48 Harbour Lane<br>
      Halifax, Canada B3H
    </address>
  </section>

</body>
</html>
```